Maplecrest Disability - Social Security Disability Attorneys

Our company is expanding to attract clients nationwide for our social security disability practice. We have a logo, but I am looking for a creative and elegant letterhead that projects an image of being technologically advanced but still professional enough for the legal field. I am looking for the "wow factor" combined with this is still professional enough for a law practice.

Requesting letterhead and business card design
Updates

Had to update and change the logo. The previous logo had a typo. Please send updates with the new logo for consideration. The letterhead and business cards should be professional enough to be used for a law firm. Thanks.

Industry/Entity Type

Law Practice, Law Firm, Healthcare Industry, Government

Colors

Designer to choose colors to be used in the design.

Requirements
Nice to have
• **Please create a vertical design for the business card**

```html
<!DOCTYPE html>
<html lang="en">
<head>
<meta charset="utf-8">
<title>Maplecrest Disability Letterhead</title>
<link rel="stylesheet" href="https://fonts.googleapis.com/css2?family=Lato:wght@400;700&family=Dancing+Script:wght@500&display=swap">
<style>
  :root {
    --bg: #dcdcdc;
    --paper: #ffffff;
    --ink: #2b2b2b;
    --brand-blue: #4a73e8;
    --brand-orange: #f7842a;
  }
  * { margin: 0; padding: 0; box-sizing: border-box; }
  html, body { width: 1200px; height: 800px; overflow: hidden; }
  body {
    background: var(--bg);
    font-family: "Lato", sans-serif;
    color: var(--ink);
    position: relative;
  }
  .sheet {
    position: absolute;
    top: 111px;
    width: 413px;
    height: 575px;
    background: var(--paper);
    overflow: hidden;
  }
  .sheet--letter { left: 165px; }
  .sheet--blank { left: 611px; }

  .brand {
    position: absolute;
    left: 23px;
    top: 49px;
    display: flex;
    align-items: center;
    gap: 5px;
  }
  .brand__dot {
    width: 7px; height: 7px;
    border-radius: 50%;
    background: var(--brand-orange);
  }
  .brand__name {
    font-size: 10px;
    font-weight: 400;
    letter-spacing: 1.1px;
    text-transform: uppercase;
    color: var(--brand-blue);
  }

  .contact {
    position: absolute;
    left: 290px;
    top: 28px;
    height: 48px;
    border-left: 1px solid var(--brand-orange);
    padding-left: 5px;
    font-size: 6.6px;
    line-height: 1;
    color: #111;
  }
  .contact__line { display: flex; align-items: center; gap: 4px; height: 9.5px; white-space: nowrap; }
  .contact__line--gap { margin-top: 2px; }
  .contact__icon { width: 6px; height: 6px; flex: none; }

  .letter {
    position: absolute;
    left: 23px;
    top: 118px;
    width: 368px;
    font-size: 8.3px;
    line-height: 9px;
  }
  .letter__date { font-size: 8.8px; margin-bottom: 10px; }
  .letter__block { margin-bottom: 10px; }
  .letter__salutation { font-size: 10px; font-weight: 700; margin-bottom: 11px; opacity: .9; }
  .letter__para { text-align: justify; margin-bottom: 9px; }
  .letter__closing { margin-top: 20px; }
  .letter__signature {
    font-family: "Dancing Script", cursive;
    font-size: 20px;
    line-height: 1;
    margin-top: 10px;
    margin-left: 2px;
  }

  .footer-band {
    position: absolute;
    left: 0;
    right: 0;
    bottom: 0;
  }
  .footer-band__rule {
    height: 3px;
    background: var(--brand-orange);
    margin-bottom: 4px;
  }
  .footer-band__fill {
    height: 34px;
    background: var(--brand-blue);
  }
</style>
</head>
<body>

  <section class="sheet sheet--letter">
    <div class="brand">
      <span class="brand__dot"></span>
      <span class="brand__name">Maplecrest Disability</span>
    </div>
    <div class="contact">
      <div class="contact__line">Suite 4, Level 12, Alder</div>
      <div class="contact__line">Street Brookfield NSW 2100</div>
      <div class="contact__line contact__line--gap">
        <svg class="contact__icon" viewBox="0 0 10 10"><path d="M2 1l2 0 1 2.5-1.3 1a5 5 0 0 0 2.5 2.5l1-1.3L9.7 7v2a1 1 0 0 1-1 1A8 8 0 0 1 1 2a1 1 0 0 1 1-1z" fill="var(--brand-orange)"/></svg>
        555-014-2290
      </div>
      <div class="contact__line">
        <svg class="contact__icon" viewBox="0 0 10 10"><rect x="0.5" y="2" width="9" height="6" fill="var(--brand-orange)"/><path d="M0.5 2l4.5 3.5L9.5 2" fill="none" stroke="#fff" stroke-width="0.8"/></svg>
        info@maplecrestdisability.com
      </div>
      <div class="contact__line">
        <svg class="contact__icon" viewBox="0 0 10 10"><circle cx="5" cy="5" r="4.5" fill="var(--brand-orange)"/><path d="M0.5 5h9M5 0.5c-2 2.5-2 6.5 0 9M5 0.5c2 2.5 2 6.5 0 9" fill="none" stroke="#fff" stroke-width="0.6"/></svg>
        www.maplecrestdisability.com
      </div>
    </div>

    <article class="letter">
      <p class="letter__date">January-03-2020</p>
      <p class="letter__block">Mr, Alan Reed<br>President</p>
      <p class="letter__block">Brightline Corporation<br>123 Street Name, Suite# 10<br>City, State, 120023</p>
      <p class="letter__salutation">Dear Mr, Alan</p>
      <p class="letter__para">Lorem ipsum dolor sit amet, consectetur adipisicing elit, sed do eiusmod tempor incididunt ut labore et dolore magna aliqua. Ut enim ad minim veniam, quis nostrud exercitation ullamco laboris nisi ut aliquip ex ea commodo consequat. Duis aute irure dolor in reprehenderit in voluptate velit esse cillum dolore eu fugiat nulla pariatur.</p>
      <p class="letter__para">Lorem ipsum dolor sit amet, consectetur adipisicing elit, sed do eiusmod tempor incididunt ut labore et dolore magna aliqua. Ut enim ad minim veniam, quis nostrud exercitation ullamco laboris nisi ut aliquip ex ea commodo consequat. Duis aute irure dolor in reprehenderit in voluptate velit esse cillum dolore eu fugiat nulla pariatur.</p>
      <p class="letter__para">Lorem ipsum dolor sit amet, consectetur adipisicing elit, sed do eiusmod tempor incididunt ut labore et dolore magna aliqua. Ut enim ad minim veniam, quis nostrud exercitation ullamco laboris nisi ut aliquip ex ea commodo consequat.</p>
      <p class="letter__para">Excepteur sint occaecat cupidatat non proident, sunt in culpa qui officia deserunt mollit anim id est laborum. re et dolore magnam aliquam quaerat voluptatem.</p>
      <p class="letter__closing">Regards</p>
      <p class="letter__signature">Daniel Hart</p>
    </article>

    <div class="footer-band" aria-hidden="true">
      <div class="footer-band__rule"></div>
      <div class="footer-band__fill"></div>
    </div>
  </section>

  <section class="sheet sheet--blank">
    <div class="brand">
      <span class="brand__dot"></span>
      <span class="brand__name">Maplecrest Disability</span>
    </div>
    <div class="contact">
      <div class="contact__line">Suite 4, Level 12, Alder</div>
      <div class="contact__line">Street Brookfield NSW 2100</div>
      <div class="contact__line contact__line--gap">
        <svg class="contact__icon" viewBox="0 0 10 10"><path d="M2 1l2 0 1 2.5-1.3 1a5 5 0 0 0 2.5 2.5l1-1.3L9.7 7v2a1 1 0 0 1-1 1A8 8 0 0 1 1 2a1 1 0 0 1 1-1z" fill="var(--brand-orange)"/></svg>
        555-014-2290
      </div>
      <div class="contact__line">
        <svg class="contact__icon" viewBox="0 0 10 10"><rect x="0.5" y="2" width="9" height="6" fill="var(--brand-orange)"/><path d="M0.5 2l4.5 3.5L9.5 2" fill="none" stroke="#fff" stroke-width="0.8"/></svg>
        info@maplecrestdisability.com
      </div>
      <div class="contact__line">
        <svg class="contact__icon" viewBox="0 0 10 10"><circle cx="5" cy="5" r="4.5" fill="var(--brand-orange)"/><path d="M0.5 5h9M5 0.5c-2 2.5-2 6.5 0 9M5 0.5c2 2.5 2 6.5 0 9" fill="none" stroke="#fff" stroke-width="0.6"/></svg>
        www.maplecrestdisability.com
      </div>
    </div>

    <div class="footer-band" aria-hidden="true">
      <div class="footer-band__rule"></div>
      <div class="footer-band__fill"></div>
    </div>
  </section>

</body>
</html>
```